Brenford SMHO Covid-19 Vaccine Advertisement (Digital + Print)

The client is needing an advertisement that will run during Football and Soccer Season to advertise getting vaccinated for the Covid-19 Shot.
Request - Sports theme related, Scoreboard, Teams match up, covid-19 vs texas theme

Client - Brenford Parish Senior and Mobility Help Office

Various Ad types:
Digital Marketing Insertion Orders
- Door Hanger
- Front Page Note
- Insert Schedule

Print + Digital Insertion Orders
- Print Ads
- Email Marketing
- Banner Ads

Must include: logo and brand colors and 1-888-555-0147, and #ArmReadyNowOK and needs to be an English version and a Spanish Version

Message Ideas to incorporate - a variation - do not use all in one ad
Brenford vs COVID
Let’s win this together!
#VaccineSavesLives
#CancelCOVID
#GetVaccinated
#GetBoosted
#GetProtected

```html
<!DOCTYPE html>
<html lang="en">
<head>
<meta charset="utf-8">
<title>Brenford vs COVID – Let's win this together</title>
<link rel="stylesheet" href="https://fonts.googleapis.com/css2?family=Montserrat:ital,wght@0,600;0,700;1,200;1,800;1,900&display=swap">
<style>
  :root {
    --navy: #13245a;
    --navy-deep: #0b1640;
    --red: #d81e25;
    --red-dark: #8f0f14;
    --white: #ffffff;
    --field: #3f8f2a;
    --field-dark: #1f5216;
    --sky: #1c2b3a;
    --stand: #4a5563;
    --virus: #2e7a54;
    --virus-dark: #1b4f36;
    --kit: #b8262c;
    --green-tag: #6cae2d;
    --purple: #5a5da8;
    --brand-ink: #2b2f6b;
    --brand-dot: #e7b62a;
  }
  * { margin: 0; padding: 0; box-sizing: border-box; }
  html, body { width: 848px; height: 1200px; overflow: hidden; background: var(--white); }
  .poster { position: relative; width: 848px; height: 1200px; overflow: hidden; font-family: "Montserrat", sans-serif; background: var(--white); }

  .stadium-scene {
    position: absolute; left: 0; top: 0; width: 848px; height: 1005px;
    background:
      radial-gradient(ellipse 60% 30% at 50% 55%, rgba(255,255,255,.35), transparent 70%),
      linear-gradient(180deg, var(--sky) 0%, #33495c 22%, var(--stand) 45%, #5c6470 60%, var(--field) 70%, #4ea335 82%, var(--field-dark) 100%);
  }
  .pitch-lines { position: absolute; left: 0; top: 0; width: 848px; height: 1005px; }

  .score-panel {
    position: absolute; left: 52px; top: 175px; width: 744px; height: 330px;
    background: linear-gradient(180deg, rgba(19,36,90,.95) 0%, rgba(19,36,90,.75) 70%, rgba(19,36,90,0) 100%);
  }
  .score-bar {
    position: absolute; left: 30px; top: 145px; width: 788px; height: 30px;
    background: linear-gradient(180deg, #2c3f86, var(--navy-deep));
    clip-path: polygon(0 0, 100% 0, 97% 100%, 3% 100%);
  }
  .hashtag-tab {
    position: absolute; left: 249px; top: 106px; width: 350px; height: 39px;
    background: linear-gradient(180deg, var(--red), var(--red-dark));
    clip-path: polygon(4% 0, 96% 0, 100% 100%, 0 100%);
    color: var(--white); font-weight: 800; font-style: italic; font-size: 22px;
    display: flex; align-items: center; justify-content: center;
  }
  .score-chip {
    position: absolute; left: 337px; top: 179px; width: 174px; height: 26px;
    background: linear-gradient(180deg, #ffffff, #cfd3db);
    clip-path: polygon(6% 0, 94% 0, 100% 100%, 0 100%);
    display: flex; align-items: center; justify-content: space-between; padding: 0 22px;
    font-weight: 800; font-size: 15px; color: var(--navy-deep);
  }
  .score-chip .clock { background: var(--navy-deep); color: var(--white); padding: 3px 8px; font-size: 13px; }

  .virus-art {
    position: absolute; left: 542px; top: 270px; width: 186px; height: 186px; border-radius: 50%;
    background: radial-gradient(circle at 40% 35%, var(--virus), var(--virus-dark));
  }
  .player-photo {
    position: absolute; left: 172px; top: 300px; width: 250px; height: 552px;
    background: linear-gradient(180deg, #c99477 0%, var(--kit) 18%, var(--kit) 42%, #141414 52%, #141414 100%);
    border-radius: 110px 110px 30px 30px; opacity: .88;
  }

  .team-name {
    position: absolute; top: 226px; color: var(--white);
    font-weight: 800; font-style: italic; font-size: 46px; letter-spacing: -.5px;
  }
  .team-home { left: 136px; }
  .team-away { left: 532px; }
  .versus {
    position: absolute; left: 338px; top: 322px; color: var(--white);
    font-weight: 900; font-style: italic; font-size: 132px; letter-spacing: -12px; line-height: 1;
    transform: scaleY(1.35); transform-origin: top left; opacity: .95;
  }
  .slash { position: absolute; left: 0; top: 0; width: 848px; height: 1005px; pointer-events: none; }

  .slogan {
    position: absolute; left: 496px; top: 598px; color: var(--white);
    font-weight: 800; font-style: italic; font-size: 70px; line-height: 78px; letter-spacing: -1px;
  }
  .slogan-strong {
    position: absolute; left: 94px; top: 842px; color: var(--white);
    font-weight: 200; font-style: italic; font-size: 106px; line-height: 1; letter-spacing: 0;
  }

  .footer-curve { position: absolute; left: 0; top: 940px; width: 848px; height: 260px; }
  .footer-tag {
    position: absolute; left: 69px; top: 1066px; color: var(--green-tag);
    font-weight: 800; font-style: italic; font-size: 28px;
  }
  .footer-phone {
    position: absolute; left: 66px; top: 1096px; color: var(--purple);
    font-weight: 800; font-style: italic; font-size: 56px; letter-spacing: -1px;
  }
  .brand-block {
    position: absolute; left: 572px; top: 1010px; width: 226px;
    display: flex; flex-direction: column; align-items: center; gap: 22px;
  }
  .brand-dot { width: 72px; height: 72px; border-radius: 50%; background: var(--brand-dot); }
  .brand-name {
    color: var(--brand-ink); font-weight: 700; font-size: 14px; line-height: 18px;
    text-align: center; text-transform: uppercase;
  }
</style>
</head>
<body>
<main class="poster">
  <div class="stadium-scene" role="img" aria-label="Floodlit soccer stadium at night with packed stands and a green pitch"></div>
  <svg class="pitch-lines" viewBox="0 0 848 1005" aria-hidden="true">
    <line x1="0" y1="815" x2="848" y2="815" stroke="#ffffff" stroke-opacity=".8" stroke-width="3"/>
    <ellipse cx="400" cy="815" rx="300" ry="38" fill="none" stroke="#ffffff" stroke-opacity=".8" stroke-width="3"/>
  </svg>

  <div class="score-panel"></div>
  <div class="score-bar"></div>
  <div class="hashtag-tab">#ArmReadyNowOK</div>
  <div class="score-chip"><span>3</span><span class="clock">90:00</span><span>0</span></div>

  <div class="virus-art" role="img" aria-label="Illustration of a green coronavirus particle"></div>
  <div class="player-photo" role="img" aria-label="Soccer player in a red jersey striking the ball mid-kick"></div>

  <div class="team-name team-home">Brenford</div>
  <div class="team-name team-away">COVID</div>
  <div class="versus">VS</div>

  <svg class="slash" viewBox="0 0 848 1005" aria-hidden="true">
    <line x1="509" y1="55" x2="350" y2="735" stroke="#ffffff" stroke-width="2.5" stroke-opacity=".9"/>
  </svg>

  <div class="slogan">Let’s<br>win<br>this</div>
  <div class="slogan-strong">TOGETHER!</div>

  <svg class="footer-curve" viewBox="0 0 848 260" preserveAspectRatio="none" aria-hidden="true">
    <path d="M0 8 Q424 110 848 8 L848 260 L0 260 Z" fill="#ffffff"/>
  </svg>
  <div class="footer-tag">#GetBoosted</div>
  <div class="footer-phone">1-888-555-0147</div>
  <div class="brand-block">
    <span class="brand-dot"></span>
    <span class="brand-name">Brenford Parish Senior and Mobility Help Office</span>
  </div>
</main>
</body>
</html>
```